Family-owned company selling organic landscaping and gardening products needs new labels.

We need label designs initially for 6 products, the designs should be unique for each product but have common design elements. The products are organic and used in landscaping, gardening and horticulture industries. Products are used commercially and residentially. The products encourage root growth and soil health, so that could be featured in the label along with plants, trees, etc. We like the colors, the sunburst background and the art deco vibe in the label designs provided for inspiration, but we are open to other ideas as well. We are also providing a sample of current labels (bland, boring) for reference. We are also providing a copy of our new logo which we like but are open to suggestions. We would like to start with the label for our TERRA BLEND product.

```html
<!DOCTYPE html>
<html lang="en">
<head>
<meta charset="utf-8">
<title>Terra Blend Label</title>
<link rel="stylesheet" href="https://fonts.googleapis.com/css2?family=Righteous&family=Baloo+2:wght@600;700&display=swap">
<style>
  :root {
    --page: #d0d1d3;
    --red-core: #e51f2e;
    --red-mid: #c8213a;
    --red-edge: #a8213b;
    --maroon: #7a1f30;
    --title-shadow: #4a0f17;
    --pill: #231f20;
    --cream: #fde7ea;
    --white: #ffffff;
    --ink: #1b1b1b;
  }
  * { margin: 0; padding: 0; box-sizing: border-box; }
  html, body { width: 903px; height: 1200px; overflow: hidden; background: var(--page); }
  .label {
    position: absolute; left: 70px; top: 20px; width: 763px; height: 1160px;
    overflow: hidden;
    background:
      repeating-radial-gradient(circle at 50% 40%, rgba(255,255,255,0) 0 38px, rgba(120,10,30,0.07) 38px 76px),
      radial-gradient(circle at 50% 40%, var(--red-core) 0%, var(--red-mid) 38%, var(--red-edge) 70%);
  }
  .title {
    position: absolute; left: 0; right: 0; top: 58px;
    font-family: "Righteous", sans-serif; font-size: 186px; line-height: 206px;
    color: var(--white); text-align: center; letter-spacing: 2px;
    text-shadow: 4px 5px 0 var(--title-shadow);
  }
  .tagline-pill {
    position: absolute; left: 59px; top: 498px; width: 640px; height: 114px;
    border-radius: 57px; background: var(--pill);
    display: flex; flex-direction: column; justify-content: center; align-items: center;
    font-family: "Baloo 2", sans-serif; font-weight: 700; font-size: 33px; line-height: 48px;
    color: var(--white);
  }
  .classification {
    position: absolute; left: 0; right: 0; top: 626px;
    font-family: "Righteous", sans-serif; font-size: 29px; line-height: 35px;
    color: var(--cream); text-align: center; letter-spacing: 0.5px;
  }
  .botanical-art {
    position: absolute; left: 0; top: 690px; width: 763px; height: 240px;
    background: linear-gradient(180deg, rgba(90,15,25,0) 0%, rgba(90,15,25,0.22) 100%);
  }
  .ground { position: absolute; left: 0; top: 0; }
  .brand-badge {
    position: absolute; left: 99px; top: 938px; width: 182px; height: 182px;
    border-radius: 50%; background: var(--white); border: 6px solid var(--ink);
    display: flex; align-items: center; justify-content: center; text-align: center;
    font-family: "Baloo 2", sans-serif; font-weight: 700; font-size: 36px; line-height: 36px;
    color: var(--ink);
  }
  .pack-info {
    position: absolute; left: 299px; top: 996px;
    font-family: "Baloo 2", sans-serif; font-weight: 700; font-size: 29px; line-height: 44px;
    color: var(--white);
  }
</style>
</head>
<body>
  <div class="label">
    <div class="title">TERRA<br>BLEND</div>
    <div class="tagline-pill">
      <span>Endo-Ecto Mycorrhizal Inoculum</span>
      <span>For Most Plants</span>
    </div>
    <div class="classification">AUXILIARY SOIL AND PLANT SUBSTANCE<br>NON PLANT FOOD INGREDIENT</div>
    <div class="botanical-art" role="img" aria-label="Line drawing of wildflowers, herbs and leafy stems rising from the ground"></div>
    <svg class="ground" width="763" height="1160" viewBox="0 0 763 1160" aria-hidden="true">
      <path fill="#7a1f30" d="M0 928 C40 920 70 900 110 895 C160 890 180 905 220 903 C260 900 280 878 320 880 C350 882 380 905 420 908 C460 910 480 895 520 893 C560 892 590 910 630 912 C680 914 720 900 763 910 L763 1160 L0 1160 Z"/>
    </svg>
    <div class="brand-badge">Root<br>Hollow</div>
    <div class="pack-info">500 – 4 gram Terra Blend Paks<br>Net Weight: 4.41 lbs (2.0 kg)</div>
  </div>
</body>
</html>
```